Law Offices business card

Hi there, I'll need business card for the Law Offices of Colin Matheny. The information must convey his strategic approach and quick resolution to complex business litigation needs. Please emphasize Civil Litigation, Corporate Law, Business Governance and Real Estate Law. Colin has over 25 years of experience in these fields.The card should be modern and edgy and the message should be clear. Please consult his current website for ideas.

```html
<!DOCTYPE html>
<html lang="en">
<head>
<meta charset="utf-8">
<title>Law Offices of Colin Matheny – Business Card</title>
<link rel="stylesheet" href="https://fonts.googleapis.com/css2?family=Libre+Baskerville&family=Open+Sans:wght@400;600;700&display=swap">
<style>
  :root {
    --backdrop: #2b2d31;
    --card: #ffffff;
    --accent: #f26a1b;
    --accent-faint: #fbe3d3;
    --ring-faint: #e6e6e6;
    --ink: #1d1d1d;
    --ink-muted: #555555;
    --divider: #9a9a9a;
  }
  * { box-sizing: border-box; margin: 0; padding: 0; }
  html, body { width: 1200px; height: 864px; overflow: hidden; }
  body {
    background: var(--backdrop);
    font-family: "Open Sans", Arial, sans-serif;
    color: var(--ink);
  }
  .canvas {
    width: 1200px; height: 864px;
    display: flex; flex-direction: column;
    align-items: center; justify-content: center;
    gap: 44px;
  }
  .card {
    position: relative;
    width: 620px; height: 354px;
    background: var(--card);
    overflow: hidden;
    box-shadow: 0 10px 28px rgba(0,0,0,.35);
  }
  .firm-name { font-family: "Libre Baskerville", Georgia, serif; line-height: 1; }
  .firm-name__main { color: var(--accent); display: block; }
  .firm-name__sub { color: var(--ink-muted); display: block; }

  /* front */
  .card--front .brand {
    position: absolute; left: 150px; top: 100px;
    display: flex; align-items: center;
  }
  .brand__dot {
    width: 88px; height: 68px; border-radius: 50%;
    background: var(--accent);
    border: 3px solid #555;
  }
  .brand__rule {
    width: 2px; height: 84px; background: var(--divider);
    margin: 0 18px 0 14px;
  }
  .card--front .firm-name__main { font-size: 31px; letter-spacing: .5px; }
  .card--front .firm-name__sub { font-size: 15.5px; margin-top: 4px; letter-spacing: .3px; }
  .services {
    position: absolute; left: 0; right: 0; top: 218px;
    text-align: center; font-weight: 600; font-size: 15.5px; line-height: 1.6;
  }
  .services__sep { margin: 0 10px; }

  /* back */
  .card--back .firm-name { position: absolute; left: 34px; top: 26px; }
  .card--back .firm-name__main { font-size: 33px; letter-spacing: .5px; }
  .card--back .firm-name__sub { font-size: 17px; margin-top: 3px; letter-spacing: .3px; }
  .watermark {
    position: absolute; left: 300px; top: 60px;
    width: 330px; height: 300px; border-radius: 50%;
    background: var(--accent-faint);
    border: 14px solid var(--ring-faint);
  }
  .person { position: absolute; left: 34px; top: 116px; }
  .person__name { color: var(--accent); font-weight: 700; font-size: 19px; }
  .person__role { font-size: 13px; margin-left: 2px; }
  .address { position: absolute; left: 34px; top: 178px; font-size: 14px; line-height: 1.35; }
  .contacts { position: absolute; left: 34px; top: 230px; list-style: none; font-size: 14px; }
  .contacts li { display: flex; align-items: center; gap: 9px; height: 22px; }
  .contacts svg { width: 12px; height: 12px; fill: var(--accent); flex: none; }
</style>
</head>
<body>
<main class="canvas">
  <section class="card card--front" aria-label="Card front">
    <div class="brand">
      <div class="brand__dot" aria-hidden="true"></div>
      <div class="brand__rule" aria-hidden="true"></div>
      <h1 class="firm-name">
        <span class="firm-name__main">LAW OFFICES</span>
        <span class="firm-name__sub">OF COLIN MATHENY</span>
      </h1>
    </div>
    <p class="services">
      Business Litigation<span class="services__sep">|</span>Real Estate<br>
      Tittle and Closing Services
    </p>
  </section>

  <section class="card card--back" aria-label="Card back">
    <div class="watermark" aria-hidden="true"></div>
    <h2 class="firm-name">
      <span class="firm-name__main">LAW OFFICES</span>
      <span class="firm-name__sub">OF COLIN MATHENY</span>
    </h2>
    <div class="person">
      <p class="person__name">Colin Matheny</p>
      <p class="person__role">Attorney</p>
    </div>
    <address class="address" style="font-style:normal">
      118B Harbor Lane<br>Palm Shores, Florida 33412
    </address>
    <ul class="contacts">
      <li><svg viewBox="0 0 12 12" aria-hidden="true"><path d="M2.4 0.8 4.2 2.8 3.3 4.2c.7 1.6 2.1 3 3.6 3.6l1.4-.9 2 1.8-1 2C5.5 10.6 1.3 6.4.7 2.1z"/></svg>561-555-0148</li>
      <li><svg viewBox="0 0 12 12" aria-hidden="true"><path d="M3 0h6v3H3zM0 4h12v6H9.5v2h-7v-2H0zM3.5 8v3h5V8z"/></svg>561-555-0193</li>
      <li><svg viewBox="0 0 12 12" aria-hidden="true"><path d="M0 2h12v1L6 7 0 3zM0 4.2 6 8.2l6-4V10H0z"/></svg>colin@mathenylegal.com</li>
      <li><svg viewBox="0 0 12 12" aria-hidden="true"><circle cx="6" cy="6" r="5.5"/></svg>www.mathenylegal.com</li>
    </ul>
  </section>
</main>
</body>
</html>
```